Commercial, Public Works, Contractor needs a modern web design

We are a General and Engineering contracting firm with vast experience in our industry. Our focus is on Commercial, Tenant Improvement, Restaurants, and Public Works. We are opening a new business and would like that excitement and energy to show through the new web design. The colors we like are black, red and grey, we are open to color ideas. Attached is our logo design.

Industry/Entity Type

Restaurant

```html
<!DOCTYPE html>
<html lang="en">
<head>
<meta charset="utf-8">
<title>Kelvara Build – General Contractor and Engineer</title>
<link href="https://fonts.googleapis.com/css2?family=Montserrat:wght@400;500;600;700&family=Roboto:wght@400;500&family=Open+Sans:wght@400;600&display=swap" rel="stylesheet">
<style>
:root{
  --red:#a3000f;
  --red-bright:#c0101d;
  --ink:#111111;
  --text:#444444;
  --muted:#8a8a8a;
  --dark:#1b1b1b;
  --darker:#0c0c0c;
  --white:#ffffff;
  --line:#dddddd;
}
*{margin:0;padding:0;box-sizing:border-box}
html,body{width:717px;height:1200px;overflow:hidden;background:var(--white)}
body{position:relative;font-family:'Roboto',sans-serif;color:var(--text)}
.abs{position:absolute}

/* hero */
.hero{left:0;top:0;width:717px;height:386px;background:linear-gradient(100deg,#c9ccd2 0%,#a9b4c4 25%,#d8c3b3 50%,#e9e3de 70%,#cfd3d8 100%)}
.site-header{left:0;top:0;width:717px;height:72px;background:rgba(255,255,255,.88)}
.brand{left:66px;top:26px;display:flex;align-items:center;gap:6px;font-family:'Montserrat',sans-serif;font-weight:700;font-size:12px;color:var(--red);letter-spacing:.3px}
.brand .mark{width:16px;height:16px;border-radius:50%;background:var(--red)}
.nav{top:33px;font-family:'Montserrat',sans-serif;font-weight:500;font-size:7.5px;color:var(--ink)}
.nav.active{color:var(--red)}
.hero-caption{left:117px;top:274px;width:484px;height:68px;background:rgba(255,255,255,.78);text-align:center}
.hero-caption h1{margin-top:17px;font-family:'Montserrat',sans-serif;font-weight:500;font-size:19px;color:var(--red)}
.hero-caption p{margin-top:4px;font-family:'Montserrat',sans-serif;font-weight:600;font-size:6.6px;color:var(--ink)}
.dot{top:371px;width:6px;height:6px;border-radius:50%;background:var(--ink)}
.dot.on{background:var(--red)}

/* welcome */
.section-title{left:0;width:717px;text-align:center;font-family:'Montserrat',sans-serif;font-weight:500;font-size:16px;color:var(--ink)}
.lead{left:70px;width:577px;text-align:center;font-size:7.3px;line-height:15.2px;color:var(--text)}
.btn{display:flex;align-items:center;justify-content:center;background:var(--red);color:var(--white);border-radius:4px;font-family:'Montserrat',sans-serif;font-weight:500}
.btn-main{left:316px;top:500px;width:84px;height:30px;font-size:9px}

/* services */
.services{left:0;top:518px;width:717px;height:243px;background:linear-gradient(180deg,#fbf3ec 0%,#f1ece7 50%,#e9e8e6 100%)}
.service{top:582px;width:134px}
.service .photo{width:134px;height:103px;border:2px solid var(--white);box-shadow:0 0 2px rgba(0,0,0,.25)}
.service h3{margin-top:10px;font-family:'Montserrat',sans-serif;font-weight:600;font-size:9.6px;color:var(--red-bright)}
.service p{margin-top:3px;font-size:6.7px;line-height:12px;color:var(--text)}

/* projects */
.projects{left:0;top:761px;width:717px;height:225px;background:var(--dark)}
.projects .section-title{color:var(--white)}
.lead.dark{color:#a8a8a8}
.project{top:848px;width:181px;height:116px}
.project .label{position:absolute;left:0;top:42px;width:181px;height:32px;background:rgba(20,20,20,.72);display:flex;align-items:center;justify-content:center;font-family:'Montserrat',sans-serif;font-size:9.5px;color:var(--white)}

/* footer */
.contact-panel{left:0;top:986px;width:251px;height:174px;background:var(--darker)}
.info-panel{left:251px;top:986px;width:466px;height:174px;background:var(--white)}
.foot-title{font-family:'Montserrat',sans-serif;font-weight:500;font-size:10.5px}
.contact-panel .foot-title{color:var(--white)}
.info-panel .foot-title{color:var(--ink)}
.contact-item{left:67px;display:flex;gap:8px;font-family:'Open Sans',sans-serif;font-size:6.6px;line-height:11px;color:#bdbdbd}
.contact-item strong{color:var(--white);font-weight:600;font-size:7.4px}
.contact-item svg{flex:none;margin-top:1px}
.social{top:1122px;width:14px;height:14px;border-radius:50%}
.post-head{font-family:'Roboto',sans-serif;font-size:8.4px;line-height:12px;color:var(--ink)}
.date{font-family:'Roboto',sans-serif;font-size:12.5px;letter-spacing:1px;color:#333}
.post-body{font-family:'Open Sans',sans-serif;font-size:6.6px;line-height:14px;color:var(--text)}
.btn-small{width:71px;height:24px;font-size:7.4px}
.bottom-bar{left:0;top:1160px;width:717px;height:40px;background:var(--darker);font-size:6.6px;color:#9a9a9a}
</style>
</head>
<body>

<div class="abs hero" role="img" aria-label="Hero photo: engineer in hard hat shaking hands, holding rolled plans"></div>
<header class="abs site-header"></header>
<div class="abs brand"><span class="mark"></span>KELVARA BUILD</div>
<nav>
  <span class="abs nav active" style="left:293px">HOME</span>
  <span class="abs nav" style="left:347px">ABOUT US</span>
  <span class="abs nav" style="left:416px">SERVICES</span>
  <span class="abs nav" style="left:483px">PROJECTS</span>
  <span class="abs nav" style="left:552px">CONTACT US</span>
  <span class="abs nav" style="left:630px">BLOG</span>
</nav>
<div class="abs hero-caption">
  <h1>CREATING THE FUTURE</h1>
  <p>LOREM IPSUM DOLOR SIT AMET, CONSECTETUER ADIPISCING ELIT, SED DIAM NONUMMY NIBH</p>
</div>
<span class="abs dot" style="left:345px"></span>
<span class="abs dot on" style="left:355px"></span>
<span class="abs dot" style="left:365px"></span>

<h2 class="abs section-title" style="top:419px">WELCOME TO KELVARA BUILD</h2>
<p class="abs lead" style="top:444px">Ut wisi enim ad minim veniam, quis nostrud exerci tation ullamcorper suscipit lobortis nisl ut aliquip ex ea commodo consequat. Duis autem vel eum iriure dolor in hendrerit in vulputate velit esse molestie consequat, vel illum dolore eu feugiat nulla facilisis at vero eros et accumsan et iusto odio dignissim qui blandit praesent luptatum zzril delenit augue duis dolore te feugait nulla facilisi.</p>

<section class="abs services" role="img" aria-label="Faint city skyline background"></section>
<a class="abs btn btn-main">READ MORE</a>
<h2 class="abs section-title" style="top:550px">OUR SERVICES</h2>
<div class="abs service" style="left:67px">
  <div class="photo" role="img" aria-label="Glass office towers against blue sky" style="background:linear-gradient(135deg,#1e4f8a,#7aa6d3 50%,#2a3340)"></div>
  <h3>COMMERCIAL</h3>
  <p>Lorem ipsum dolor sit amet, consectetuer adipiscing elit, sed diam nonummy nibh euismod tincidunt.</p>
</div>
<div class="abs service" style="left:216px">
  <div class="photo" role="img" aria-label="Wall of golden gears" style="background:radial-gradient(circle at 50% 45%,#f3c766,#8a6420 55%,#3a2a14)"></div>
  <h3>TENANT IMPROVEMENT</h3>
  <p>Lorem ipsum dolor sit amet, consectetuer adipiscing elit, sed diam nonummy nibh euismod tincidunt.</p>
</div>
<div class="abs service" style="left:366px">
  <div class="photo" role="img" aria-label="Terrace lounge overlooking a lake" style="background:linear-gradient(180deg,#5d6670,#a9b8c4 40%,#6d8a6a 65%,#2c2c2c)"></div>
  <h3>RESTAURANTS</h3>
  <p>Lorem ipsum dolor sit amet, consectetuer adipiscing elit, sed diam nonummy nibh euismod tincidunt.</p>
</div>
<div class="abs service" style="left:516px">
  <div class="photo" role="img" aria-label="Business people meeting by glass facade" style="background:linear-gradient(135deg,#3c5c96,#8ea7cf 55%,#d9cdb4)"></div>
  <h3>PUBLIC WORKS</h3>
  <p>Lorem ipsum dolor sit amet, consectetuer adipiscing elit, sed diam nonummy nibh euismod tincidunt.</p>
</div>

<section class="abs projects"></section>
<h2 class="abs section-title" style="top:781px;color:var(--white)">RECENT PROJECTS</h2>
<p class="abs lead dark" style="top:806px">Duis autem vel eum iriure dolor in hendrerit in vulputate velit esse molestie consequat, vel illum dolore eu feugiat nulla facilisis at vero eros et accumsan et iusto odio dignissim qui blandit praesent luptatum zzril delenit augue duis dolore te feugait nulla facilisi.</p>
<div class="abs project" style="left:68px;background:linear-gradient(180deg,#9fc6d4,#36525c 55%,#1c2428)" role="img" aria-label="Steel and glass atrium roof">
  <div class="label">UT WISI ENIM AD MINIM</div>
</div>
<div class="abs project" style="left:268px;background:linear-gradient(180deg,#8a8a86,#3a3a36 50%,#7fa9c8)" role="img" aria-label="Steel space-frame ceiling">
  <div class="label">LOREM IPSUM DOLOR SIT</div>
</div>
<div class="abs project" style="left:468px;background:linear-gradient(180deg,#5e8cc6,#1e3557 50%,#0f1a2a)" role="img" aria-label="Skyscrapers seen from below">
  <div class="label">DUIS AUTEM VEL EUM</div>
</div>

<footer>
  <div class="abs contact-panel"></div>
  <div class="abs info-panel"></div>
  <h4 class="abs foot-title" style="left:67px;top:1010px;color:var(--white)">CONTACT US</h4>
  <div class="abs contact-item" style="top:1037px">
    <svg width="7" height="9" viewBox="0 0 7 9"><path d="M3.5 0A3.5 3.5 0 0 0 0 3.5C0 6 3.5 9 3.5 9S7 6 7 3.5A3.5 3.5 0 0 0 3.5 0z" fill="#c0101d"/><circle cx="3.5" cy="3.5" r="1.3" fill="#0c0c0c"/></svg>
    <div><strong>KELVARA BUILD</strong><br>Lorem Ipsm, Lorem Ipsm,<br>Lorem Ipsm - 123 456</div>
  </div>
  <div class="abs contact-item" style="top:1080px">
    <svg width="9" height="7" viewBox="0 0 9 7"><rect width="9" height="7" rx="1" fill="#c0101d"/><path d="M0.5 0.8L4.5 4L8.5 0.8" stroke="#0c0c0c" fill="none"/></svg>
    <div>hello@kelvarabuild.com</div>
  </div>
  <div class="abs contact-item" style="top:1100px">
    <svg width="8" height="8" viewBox="0 0 8 8"><path d="M1.5 0.5L3 2.2L2.2 3.3C2.8 4.5 3.6 5.3 4.7 5.8L5.8 5L7.5 6.5L6.6 7.6C3.5 7.4 0.6 4.5 0.4 1.4Z" fill="#c0101d"/></svg>
    <div>&nbsp;123 456 789 000</div>
  </div>
  <span class="abs social" style="left:67px;background:#2d5a9e"></span>
  <span class="abs social" style="left:85px;background:#2aa3e0"></span>
  <span class="abs social" style="left:103px;background:#d63b2b"></span>
  <span class="abs social" style="left:121px;background:#2a74b0"></span>
  <span class="abs social" style="left:139px;background:#f07a1a"></span>

  <h4 class="abs foot-title" style="left:265px;top:1010px">FROM THE BLOG</h4>
  <p class="abs post-head" style="left:266px;top:1030px;width:188px">Praesent vestibulum molestie lacus. Aenean nonummy hendrerit</p>
  <p class="abs post-body" style="left:266px;top:1057px;width:188px">Lorem ipsum dolor sit amet, conse adipiscing elit. Praesent vestibulum molestie lacus. Aenean nonummy hendrerit mauris. Phasellus porta. Fusce suscipit varius mi. Cum sociis natoque penatibus et magnis dis.</p>
  <a class="abs btn btn-small" style="left:266px;top:1120px">READ MORE</a>

  <h4 class="abs foot-title" style="left:465px;top:1010px">NEWS &amp; EVENTS</h4>
  <p class="abs date" style="left:464px;top:1033px">12 / 01/ 2015</p>
  <p class="abs post-body" style="left:466px;top:1053px;width:190px">Lorem ipsum dolor sit amet, conse adipiscing elit. Praesent vestibulum molestie lacus. Aenean nonummy hendrerit mauris. Phasellus porta. Fusce suscipit varius mi. Cum sociis natoque penatibus et magnis dis.</p>
  <a class="abs btn btn-small" style="left:466px;top:1120px">READ MORE</a>

  <div class="abs bottom-bar">
    <span class="abs" style="left:66px;top:16px">Privacy Policy &nbsp;&nbsp;|&nbsp;&nbsp; Sitemap</span>
    <span class="abs" style="right:67px;top:16px">Copyright © 2015 KELVARA BUILD. All rights reserved</span>
  </div>
</footer>

</body>
</html>
```